Natural Light/Organic/Documentary Photography Business

I like a simple, approachable, feminine, earthy/organic feel. Earth/neutral tones, nothing too loud or obnoxious. I like the watercolor look. I don't want anything too trendy or something I'll get tired of after a couple months. As far as colors, I am much more a fan of cream/taupe/blue/green...not a fan of pink or purple at all.

Target Market(s)

Weddings & Families

Industry/Entity Type

Wedding Photography

Contact Information for Business Card

website, email, phone number

Font styles to use
Other font styles liked:
• Horizontes, Gotham

Colors

Designer to choose colors to be used in the design.

Requirements
Must have
• Website: www.mirelhatchway.com
• Phone: 418.629.5073
• Email: mirel@mirelhatchway.com
Nice to have
• I like the watercolor look but its not necessary. I like simple/earthy tones. Nothing too loud or distracting. Simple & feminine without being too girly. I like an approachable/soft feel.
• Instagram: www.instagram.com/mirelhatchwayphotography/
Should not have
• NO loud colors or design or pattern. I do not want a photo of a camera or lens or anything cheesy like that.

```html
<!DOCTYPE html>
<html lang="en">
<head>
<meta charset="utf-8">
<title>Mirel Hatchway Photography — Business Card</title>
<link rel="stylesheet" href="https://fonts.googleapis.com/css2?family=Allison&family=Montserrat:wght@400&family=Quicksand:wght@300;400&display=swap">
<style>
  :root {
    --page-bg: #ffffff;
    --card-bg: #ffffff;
    --card-edge: #6f6a66;
    --ink: #6b6662;
    --wash-aqua: #cfe6e5;
    --wash-yellow: #eef2a8;
    --wash-sky: #e3eef3;
  }
  * { margin: 0; padding: 0; box-sizing: border-box; }
  html, body {
    width: 1200px;
    height: 1194px;
    overflow: hidden;
    background: var(--page-bg);
  }
  .stage {
    position: relative;
    width: 1200px;
    height: 1194px;
  }
  .business-card {
    position: absolute;
    left: 100px;
    top: 311px;
    width: 1000px;
    height: 572px;
    background: var(--card-bg);
    border: 2px solid var(--card-edge);
    overflow: hidden;
  }
  .watercolor-area {
    position: absolute;
    left: 0;
    top: 18px;
    width: 100%;
    height: 400px;
    background: linear-gradient(180deg,
      var(--wash-aqua) 0%,
      var(--wash-aqua) 55%,
      var(--wash-yellow) 75%,
      var(--wash-sky) 90%,
      rgba(255,255,255,0) 100%);
  }
  .brand {
    position: absolute;
    left: 0;
    right: 0;
    top: 92px;
    text-align: center;
    color: var(--ink);
  }
  .brand-name {
    font-family: "Allison", cursive;
    font-weight: 400;
    font-size: 150px;
    line-height: 1;
    letter-spacing: 2px;
  }
  .brand-tagline {
    margin-top: -14px;
    font-family: "Montserrat", sans-serif;
    font-size: 15px;
    letter-spacing: 9px;
    text-transform: uppercase;
    padding-left: 120px;
  }
  .contact {
    position: absolute;
    left: 0;
    right: 0;
    top: 384px;
    list-style: none;
    text-align: center;
    font-family: "Quicksand", sans-serif;
    font-weight: 300;
    font-size: 35px;
    line-height: 50px;
    color: var(--ink);
  }
</style>
</head>
<body>
  <main class="stage">
    <article class="business-card">
      <div class="watercolor-area" role="img" aria-label="Soft watercolor wash in aqua, pale yellow and light blue tones"></div>

      <header class="brand">
        <h1 class="brand-name">Mirel Hatchway</h1>
        <p class="brand-tagline">Photography</p>
      </header>

      <ul class="contact">
        <li class="contact-phone">418.629.5073</li>
        <li class="contact-email">mirel@mirelhatchway.com</li>
        <li class="contact-web">www.mirelhatchway.com</li>
      </ul>
    </article>
  </main>
</body>
</html>
```